Vortel surface design based website for technology jobs website

We need a website design for a technology job listing website, mainly aiming at 20/30/40 year old nerds. Jobs listed from multiple sources will be concatenated and organised. This website will be built with Vortel surface design (https://surfacekit.example/guidelines/) so please use their components. The design should be simple and clear, so a user can directly look for offerings that are interesting for him.

Three different pages will be needed:

1. Main jobs list page

Contains a large table (https://surfacekit.example/guidelines/components/data-tables.html#data-tables-structure), on top or next to this data-table users should be able to apply filters (select countries, select salary ranges) and somewhere an overview of the selected filters should be shown.

- A subscribe bar should be shown somewhere to allow a user to register for weekly/monthly mailings for new job offers with his preferred search filters.

2. Selected item page

If an item is clicked, a user should be able to view a job posting and it's details.

3. An advertiser should be able post his job offer.
Similar fields as https://post.ledgerworkboard.example/.
(https://surfacekit.example/guidelines/components/text-fields.html#text-fields-layout)

Target Market(s)

20/30/40 year old nerds.

Industry/Entity Type

Computer

Logo Text

TechHirePlaza.example

Number of Pages Required

3 page

Colors

Designer to choose colors to be used in the design.

Requirements
Must have
• 1. Main jobs list page
• Contains a large table (https://surfacekit.example/guidelines/components/data-tables.html#data-tables-structure), on top or next to this data-table users should be able to apply filters (select countries, select salary ranges) and somewhere an overview of the selected filters should be shown.
• - A subscribe bar should be shown somewhere to allow a user to register for weekly/monthly mailings for new job offers with his preferred search filters.
• 2. Selected item page
• If an item is clicked, a user should be able to view a job posting and it's details.
• 3. An advertiser should be able post his job offer,
• (https://surfacekit.example/guidelines/components/text-fields.html#text-fields-layout)
• Please use open fonts!

```html
<!DOCTYPE html>
<html lang="en">
<head>
<meta charset="utf-8">
<title>Veldhaven — Technology Jobs</title>
<link rel="stylesheet" href="https://fonts.googleapis.com/css2?family=Poppins:ital,wght@0,300;0,400;0,500;0,600;0,700;1,300;1,400;1,500&display=swap">
<style>
:root{
  --blue:#1565c0;
  --blue-text:#1e6fd0;
  --teal:#0e5b6f;
  --yellow:#f7d01a;
  --red:#ef3b2d;
  --ink:#222222;
  --body:#444444;
  --muted:#666666;
  --panel:#eef0f8;
  --panel-line:#d9dcea;
  --row:#ffffff;
  --footer:#1c1c1c;
  --full-green:#8fae1b;
  --part-yellow:#e8b814;
  --full-salmon:#ee7f7a;
  --part-blue:#7ea6cf;
  --full-lilac:#c99ad8;
  --part-slate:#6f8794;
}
*{margin:0;padding:0;box-sizing:border-box}
html,body{width:1200px;height:2941px;overflow:hidden}
body{position:relative;font-family:"Poppins",sans-serif;color:var(--ink);background:#fff}
a{color:inherit;text-decoration:none}

/* header */
.site-header{position:absolute;top:0;left:0;width:1200px;height:92px;background:#fff;z-index:3}
.brand{position:absolute;left:98px;top:14px;font-size:43px;font-weight:600;color:#2a2a2a;letter-spacing:-.5px}
.main-nav{position:absolute;left:526px;top:36px;display:flex;gap:30px;font-size:15px;font-weight:500;color:#222}
.btn-login{position:absolute;left:996px;top:29px;width:104px;height:36px;background:var(--blue);color:#fff;font-size:16px;font-weight:500;display:flex;align-items:center;justify-content:center;border-radius:3px}

/* hero */
.hero{position:absolute;top:92px;left:0;width:1200px;height:590px;overflow:hidden}
.hero-photo{position:absolute;inset:0;background:
  radial-gradient(ellipse at 55% 35%,#8a6f5b 0%,transparent 45%),
  linear-gradient(100deg,#6d5b4c 0%,#8b7a68 30%,#5f6f7a 55%,#4a5a45 80%,#6b7a4e 100%)}
.hero-shade{position:absolute;inset:0;background:rgba(30,25,20,.25)}
.hero-title{position:absolute;left:0;width:1200px;top:212px;text-align:center;color:#fff;font-weight:700;font-size:55px;line-height:52px;letter-spacing:.5px}
.hero-title .second{font-size:50px}
.btn-read{position:absolute;left:539px;top:343px;width:122px;height:35px;background:var(--blue);color:#fff;font-size:15px;font-weight:600;display:flex;align-items:center;justify-content:center}
.hero-dots{position:absolute;top:446px;left:565px;display:flex;gap:6px;align-items:center}
.hero-dots span{width:11px;height:11px;border-radius:50%;background:#fff}
.hero-dots span.active{width:15px;height:15px;border:3px solid rgba(255,255,255,.6);background:#fff;background-clip:content-box;padding:1px}
.hero-curve{position:absolute;left:0;top:586px;width:1200px;height:100px;z-index:2}

/* welcome */
.welcome{position:absolute;top:672px;left:98px;width:1004px;text-align:center}
.welcome h1{font-size:35px;font-weight:600;color:#222;letter-spacing:.3px}
.welcome .lead{margin-top:10px;font-size:16px;color:var(--blue-text)}
.welcome p.intro{margin-top:14px;font-size:13.5px;line-height:26px;color:var(--body)}

/* job listing */
.job-panel{position:absolute;left:98px;top:908px;width:1004px;height:754px;background:var(--panel);border:1px solid var(--panel-line)}
.job-panel h2{position:absolute;left:20px;top:50px;font-size:31px;font-weight:400;color:#333}
.filter{position:absolute;top:46px;width:190px;height:35px;border:1px solid #cfd2de;border-radius:18px;background:#fff;font-size:13px;color:#444;padding:0 18px;display:flex;align-items:center;justify-content:space-between}
.filter.countries{left:581px}
.filter.salary{left:787px}
.filter svg{width:8px;height:12px}
.table-head{position:absolute;top:128px;left:20px;width:964px;font-size:11.5px;font-weight:500;color:#333;text-transform:uppercase}
.table-head span{position:absolute;top:0}
.table-rule{position:absolute;left:20px;top:169px;width:964px;height:2px;background:#7fc6e0}
.job-row{position:absolute;left:20px;width:964px;height:84px;background:var(--row);border:1px solid #e3e5ee}
.company-mark{position:absolute;left:18px;top:20px;width:60px;height:48px;border:1px solid #d8d8d8;background:#fff;display:flex;align-items:center;justify-content:center}
.company-mark i{display:block;width:26px;height:26px;border-radius:50%}
.job-title{position:absolute;left:94px;top:16px;font-size:15.5px;color:#333;white-space:nowrap}
.company-name{position:absolute;left:94px;top:46px;font-size:12px;color:#666;display:flex;align-items:center;gap:8px}
.company-name svg{width:11px;height:11px}
.col-divider{position:absolute;top:0;width:1px;height:84px;background:#ececec}
.badge{position:absolute;left:370px;top:30px;width:90px;height:26px;border-radius:13px;color:#fff;font-size:12px;font-weight:500;display:flex;align-items:center;justify-content:center}
.badge.full-green{background:var(--full-green)}
.badge.part-yellow{background:var(--part-yellow)}
.badge.full-salmon{background:var(--full-salmon)}
.badge.part-blue{background:var(--part-blue)}
.badge.full-lilac{background:var(--full-lilac)}
.badge.part-slate{background:var(--part-slate)}
.location{position:absolute;left:495px;top:35px;font-size:12.5px;color:#333}
.expiry{position:absolute;left:675px;top:35px;font-size:12.5px;color:#333}
.btn-apply{position:absolute;left:858px;top:31px;width:90px;height:28px;border-radius:14px;background:var(--red);color:#fff;font-size:14px;font-weight:500;display:flex;align-items:center;justify-content:center}

/* pagination */
.pagination{position:absolute;top:1727px;left:491px;display:flex;align-items:center;gap:14px;font-size:14px;color:#444}
.pagination .arrow{width:24px;height:26px;background:var(--teal);display:flex;align-items:center;justify-content:center}
.pagination .arrow svg{width:8px;height:10px}
.pagination .gap{color:#aaa}

/* newsletter */
.newsletter{position:absolute;left:0;top:1833px;width:1200px;height:423px;overflow:hidden}
.newsletter-photo{position:absolute;inset:0;background:
  radial-gradient(ellipse at 20% 70%,#5a5046 0%,transparent 40%),
  radial-gradient(ellipse at 80% 60%,#4d4a3e 0%,transparent 40%),
  linear-gradient(180deg,#3a3733 0%,#2b2926 100%)}
.newsletter-shade{position:absolute;inset:0;background:rgba(0,0,0,.35)}
.newsletter h2{position:absolute;top:128px;left:0;width:1200px;text-align:center;color:#fff;font-size:39px;font-weight:600;letter-spacing:1px}
.newsletter .sub{position:absolute;top:198px;left:0;width:1200px;text-align:center;color:#fff;font-size:14.5px;font-weight:500}
.subscribe-form{position:absolute;left:351px;top:249px;width:498px;height:41px;display:flex}
.subscribe-form .field{flex:1;background:#fff;border-radius:21px 0 0 21px;font-size:12.5px;color:#555;padding-left:25px;display:flex;align-items:center}
.subscribe-form .btn-subscribe{width:126px;background:var(--red);color:#fff;font-weight:600;font-size:15px;border-radius:0 21px 21px 0;display:flex;align-items:center;justify-content:center}

/* testimonial */
.testimonial{position:absolute;left:0;top:2256px;width:1200px;height:451px}
.avatar{position:absolute;left:529px;top:68px;width:142px;height:142px;border-radius:50%;background:linear-gradient(180deg,#c9ced6 0%,#8793a3 55%,#2c3646 100%)}
.quote-mark{position:absolute;width:42px;height:32px}
.quote-mark.open{left:182px;top:188px}
.quote-mark.close{left:974px;top:326px}
.testimonial blockquote{position:absolute;left:160px;top:236px;width:880px;text-align:center;font-style:italic;font-size:13.5px;line-height:28px;color:#333}
.testimonial cite{position:absolute;left:0;top:338px;width:1200px;text-align:center;font-size:15.5px;color:#333;font-style:italic}
.testimonial cite b{font-weight:600}

/* footer */
.site-footer{position:absolute;left:0;top:2707px;width:1200px;height:234px;background:var(--footer);color:#fff}
.footer-nav{position:absolute;top:54px;left:0;width:1200px;display:flex;justify-content:center;gap:22px;font-size:14px;font-weight:500}
.footer-nav .sep{color:#ddd}
.copyright{position:absolute;top:96px;width:1200px;text-align:center;font-size:14px}
.social{position:absolute;top:142px;left:512px;display:flex;gap:7px}
.social a{width:30px;height:30px;border-radius:50%;background:#fff;display:flex;align-items:center;justify-content:center}
.social svg{width:16px;height:16px}
</style>
</head>
<body>

<header class="site-header">
  <div class="brand">Veldhaven</div>
  <nav class="main-nav">
    <a href="#">HOME</a><a href="#">ABOUT US</a><a href="#">JOBS LIST</a><a href="#">JOB OFFER</a><a href="#">CONTACT</a>
  </nav>
  <a class="btn-login" href="#">LOGIN</a>
</header>

<section class="hero">
  <div class="hero-photo" role="img" aria-label="Photo of a relaxed, smiling man leaning back at a desk with a laptop in a bright office"></div>
  <div class="hero-shade"></div>
  <h2 class="hero-title">FIND THE CAREER<br><span class="second">YOU DESERVE</span></h2>
  <a class="btn-read" href="#">READ MORE</a>
  <div class="hero-dots"><span class="active"></span><span></span><span></span><span></span></div>
</section>
<svg class="hero-curve" viewBox="0 0 1200 100" preserveAspectRatio="none" aria-hidden="true">
  <path d="M0 84 Q600 -40 1200 84 L1200 100 L0 100 Z" fill="#ffffff"/>
  <path d="M0 84 Q600 -40 1200 84" fill="none" stroke="#f7d01a" stroke-width="5"/>
</svg>

<section class="welcome">
  <h1>WELCOME TO VELDHAVEN</h1>
  <div class="lead">Search between more them 50,000 open jobs.</div>
  <p class="intro">Sed ut perspiciatis unde omnis iste natus error sit voluptatem accusantium doloremque laudantium, totam rem aperiam, eaque ipsa quae ab illo inventore veritatis et quasi architecto beatae vitae dicta sunt explicabo. Nemo enim ipsam voluptatem quia voluptas sit aspernatur aut odit aut fugit, sed quia consequuntur magni dolores eos qui ratione voluptatem sequi nesciunt.</p>
</section>

<section class="job-panel">
  <h2>JOB LISTING</h2>
  <div class="filter countries">Countries<svg viewBox="0 0 8 12"><path d="M4 0L8 5H0Z M4 12L0 7H8Z" fill="#444"/></svg></div>
  <div class="filter salary">Salary Range<svg viewBox="0 0 8 12"><path d="M4 0L8 5H0Z M4 12L0 7H8Z" fill="#444"/></svg></div>

  <div class="table-head">
    <span style="left:4px">Job Title / Company Name</span>
    <span style="left:382px">Type</span>
    <span style="left:530px">Location</span>
    <span style="left:695px">Expired Date</span>
  </div>
  <div class="table-rule"></div>

  <div class="job-row" style="top:172px">
    <div class="company-mark"><i style="background:#3aa7d8"></i></div>
    <div class="job-title">Marketing Coordinator</div>
    <div class="company-name"><svg viewBox="0 0 11 11"><path d="M0 11V3L5.5 0 11 3V11ZM2 5h2v4H2ZM7 5h2v4H7Z" fill="#555"/></svg>Company Name</div>
    <div class="col-divider" style="left:340px"></div><div class="col-divider" style="left:490px"></div><div class="col-divider" style="left:650px"></div><div class="col-divider" style="left:832px"></div>
    <div class="badge full-green">FULL TIME</div>
    <div class="location">Cupertino, CA, USA</div>
    <div class="expiry">Nov 14th , 2017</div>
    <a class="btn-apply" href="#">Apply Now</a>
  </div>

  <div class="job-row" style="top:262px">
    <div class="company-mark"><i style="background:#e4572e"></i></div>
    <div class="job-title">Looking for a project leader</div>
    <div class="company-name"><svg viewBox="0 0 11 11"><path d="M0 11V3L5.5 0 11 3V11ZM2 5h2v4H2ZM7 5h2v4H7Z" fill="#555"/></svg>Company Name</div>
    <div class="col-divider" style="left:340px"></div><div class="col-divider" style="left:490px"></div><div class="col-divider" style="left:650px"></div><div class="col-divider" style="left:832px"></div>
    <div class="badge part-yellow">PART TIME</div>
    <div class="location">Cupertino, CA, USA</div>
    <div class="expiry">Nov 14th , 2017</div>
    <a class="btn-apply" href="#">Apply Now</a>
  </div>

  <div class="job-row" style="top:352px">
    <div class="company-mark"><i style="background:#2a3e7a"></i></div>
    <div class="job-title">Front-end developer needed</div>
    <div class="company-name"><svg viewBox="0 0 11 11"><path d="M0 11V3L5.5 0 11 3V11ZM2 5h2v4H2ZM7 5h2v4H7Z" fill="#555"/></svg>Company Name</div>
    <div class="col-divider" style="left:340px"></div><div class="col-divider" style="left:490px"></div><div class="col-divider" style="left:650px"></div><div class="col-divider" style="left:832px"></div>
    <div class="badge full-salmon">FULL TIME</div>
    <div class="location">Cupertino, CA, USA</div>
    <div class="expiry">Nov 14th , 2017</div>
    <a class="btn-apply" href="#">Apply Now</a>
  </div>

  <div class="job-row" style="top:442px">
    <div class="company-mark"><i style="background:#f08a24"></i></div>
    <div class="job-title">Web Designer needed</div>
    <div class="company-name"><svg viewBox="0 0 11 11"><path d="M0 11V3L5.5 0 11 3V11ZM2 5h2v4H2ZM7 5h2v4H7Z" fill="#555"/></svg>Company Name</div>
    <div class="col-divider" style="left:340px"></div><div class="col-divider" style="left:490px"></div><div class="col-divider" style="left:650px"></div><div class="col-divider" style="left:832px"></div>
    <div class="badge part-blue">PART TIME</div>
    <div class="location">Cupertino, CA, USA</div>
    <div class="expiry">Nov 14th , 2017</div>
    <a class="btn-apply" href="#">Apply Now</a>
  </div>

  <div class="job-row" style="top:532px">
    <div class="company-mark"><i style="background:#2d8fc4"></i></div>
    <div class="job-title">Software Engineer</div>
    <div class="company-name"><svg viewBox="0 0 11 11"><path d="M0 11V3L5.5 0 11 3V11ZM2 5h2v4H2ZM7 5h2v4H7Z" fill="#555"/></svg>Company Name</div>
    <div class="col-divider" style="left:340px"></div><div class="col-divider" style="left:490px"></div><div class="col-divider" style="left:650px"></div><div class="col-divider" style="left:832px"></div>
    <div class="badge full-lilac">FULL TIME</div>
    <div class="location">Cupertino, CA, USA</div>
    <div class="expiry">Nov 14th , 2017</div>
    <a class="btn-apply" href="#">Apply Now</a>
  </div>

  <div class="job-row" style="top:622px">
    <div class="company-mark"><i style="background:#3fa64a"></i></div>
    <div class="job-title" style="font-size:14.5px">Urgent Require- Web Developer</div>
    <div class="company-name"><svg viewBox="0 0 11 11"><path d="M0 11V3L5.5 0 11 3V11ZM2 5h2v4H2ZM7 5h2v4H7Z" fill="#555"/></svg>Company Name</div>
    <div class="col-divider" style="left:340px"></div><div class="col-divider" style="left:490px"></div><div class="col-divider" style="left:650px"></div><div class="col-divider" style="left:832px"></div>
    <div class="badge part-slate">PART TIME</div>
    <div class="location">Cupertino, CA, USA</div>
    <div class="expiry">Nov 14th , 2017</div>
    <a class="btn-apply" href="#">Apply Now</a>
  </div>
</section>

<nav class="pagination">
  <a class="arrow" href="#"><svg viewBox="0 0 8 10"><path d="M6 0L1 5 6 10" fill="none" stroke="#fff" stroke-width="2"/></svg></a>
  <a href="#">1</a><a href="#">2</a><a href="#">3</a><a href="#">4</a><span class="gap">...</span><a href="#">20</a>
  <a class="arrow" href="#"><svg viewBox="0 0 8 10"><path d="M2 0L7 5 2 10" fill="none" stroke="#fff" stroke-width="2"/></svg></a>
</nav>

<section class="newsletter">
  <div class="newsletter-photo" role="img" aria-label="Photo of colleagues meeting around a table in a dim brick-walled office"></div>
  <div class="newsletter-shade"></div>
  <h2>SIGN UP FOR NEWSLETTER</h2>
  <div class="sub">REGISTER FOR WEEKLY/MONTHLY MAILINGS FOR NEW JOB OFFERS</div>
  <form class="subscribe-form">
    <div class="field">Enter your E - mail</div>
    <div class="btn-subscribe">SUBSCRIBE</div>
  </form>
</section>

<section class="testimonial">
  <div class="avatar" role="img" aria-label="Portrait photo of a man in a dark suit"></div>
  <svg class="quote-mark open" viewBox="0 0 42 32" aria-hidden="true">
    <g fill="#222">
      <circle cx="10" cy="23" r="8"/>
      <path d="M2.2 24 C1 13 6 4 16 1 L17.5 4 C11 7 8.5 12 9 17 Z"/>
      <circle cx="32" cy="23" r="8"/>
      <path d="M24.2 24 C23 13 28 4 38 1 L39.5 4 C33 7 30.5 12 31 17 Z"/>
    </g>
  </svg>
  <blockquote>Lorem ipsum dolor sit amet, consectetur adipiscing elit, sed do eiusmod tempor incididunt ut labore et dolore magna aliqua. Ut enim ad minim veniam, quis nostrud exercitation ullamco laboris nisi ut aliquip ex ea commodo consequat. Duis aute irure dolor in reprehenderit in voluptate velit esse cillum dolore eu fugiat nulla pariatur. Excepteur sint occaecat</blockquote>
  <cite><b>John Doe</b> - Nemo enim ipsam voluptatem</cite>
  <svg class="quote-mark close" viewBox="0 0 42 32" aria-hidden="true">
    <g fill="#222" transform="rotate(180 21 16)">
      <circle cx="10" cy="23" r="8"/>
      <path d="M2.2 24 C1 13 6 4 16 1 L17.5 4 C11 7 8.5 12 9 17 Z"/>
      <circle cx="32" cy="23" r="8"/>
      <path d="M24.2 24 C23 13 28 4 38 1 L39.5 4 C33 7 30.5 12 31 17 Z"/>
    </g>
  </svg>
</section>

<footer class="site-footer">
  <nav class="footer-nav">
    <a href="#">HOME</a><span class="sep">/</span><a href="#">ABOUT</a><span class="sep">/</span><a href="#">JOBS LIST</a><span class="sep">/</span><a href="#">FAQ</a><span class="sep">/</span><a href="#">CONTACT</a>
  </nav>
  <div class="copyright">2018 © Copyrights Veldhaven.All Rights Reserved</div>
  <div class="social">
    <a href="#" aria-label="Email"><svg viewBox="0 0 16 16"><rect x="2" y="4" width="12" height="8" fill="none" stroke="#1c1c1c" stroke-width="1.5"/><path d="M2 4l6 5 6-5" fill="none" stroke="#1c1c1c" stroke-width="1.5"/></svg></a>
    <a href="#" aria-label="Share"><svg viewBox="0 0 16 16"><g fill="#1c1c1c"><circle cx="4" cy="8" r="2"/><circle cx="12" cy="4" r="2"/><circle cx="12" cy="12" r="2"/></g><path d="M4 8L12 4M4 8l8 4" stroke="#1c1c1c" stroke-width="1.3"/></svg></a>
    <a href="#" aria-label="Link"><svg viewBox="0 0 16 16"><g fill="none" stroke="#1c1c1c" stroke-width="1.6"><rect x="1.5" y="6" width="7" height="4" rx="2"/><rect x="7.5" y="6" width="7" height="4" rx="2"/></g></svg></a>
    <a href="#" aria-label="Chat"><svg viewBox="0 0 16 16"><path d="M2 3h12v8H7l-3 3v-3H2Z" fill="#1c1c1c"/></svg></a>
    <a href="#" aria-label="Location"><svg viewBox="0 0 16 16"><path d="M8 1a5 5 0 0 0-5 5c0 4 5 9 5 9s5-5 5-9a5 5 0 0 0-5-5Zm0 7a2 2 0 1 1 0-4 2 2 0 0 1 0 4Z" fill="#1c1c1c"/></svg></a>
  </div>
</footer>

</body>
</html>
```